Fern Lattice Table & Chair Rentals

We need a business card for a table and chair rental company. We rent tables and chairs for weddings, funerals, business events and parties. We want something that looks clean and elegant while not being too busy. We would like colors in the green and blue hues and avoiding anything orange. We want to make sure the font is large enough to be seen easily.

Target Market(s)

Wedding & Event Rentals

Industry/Entity Type

Events

Contact Information for Business Card

Fern Lattice, sales@fernlatticerentals.com, fernlatticerentals.com, 360-555-0182

Requirements
Must have
• Easy to read font
Should not have
• Orange anywhere in the design

```html
<!DOCTYPE html>
<html lang="en">
<head>
<meta charset="utf-8">
<title>Fern Lattice Table &amp; Chair Rentals – Business Card</title>
<link rel="stylesheet" href="https://fonts.googleapis.com/css2?family=Open+Sans:wght@300;400;600&display=swap">
<style>
  :root {
    --page-bg: #ecebe7;
    --card-white: #ffffff;
    --card-shade: #f0f0f0;
    --ink: #2b2b2b;
    --ink-soft: #3c3c3c;
    --accent: #2a7f8f;
    --accent-deep: #1f6a78;
    --rule: #c9c9c9;
    --grass-light: #8fb65a;
    --grass-dark: #4d7a2e;
    --chair-white: #dfe3df;
  }
  * { box-sizing: border-box; margin: 0; padding: 0; }
  html, body { width: 1200px; height: 892px; overflow: hidden; }
  body {
    background: var(--page-bg);
    font-family: "Open Sans", Arial, sans-serif;
    color: var(--ink);
    display: flex;
    flex-direction: column;
    align-items: center;
    justify-content: center;
    gap: 56px;
  }
  .card {
    position: relative;
    width: 584px;
    height: 334px;
    background: var(--card-white);
    box-shadow: 0 6px 18px rgba(0,0,0,0.18);
    overflow: hidden;
  }

  /* ---------- front ---------- */
  .front-head {
    position: absolute; left: 0; top: 0;
    width: 262px; height: 158px;
    background: linear-gradient(180deg, var(--card-white), var(--card-shade));
    padding: 52px 0 0 30px;
  }
  .brand-name {
    font-weight: 600;
    font-size: 34px;
    line-height: 1.05;
    color: var(--ink);
  }
  .brand-tagline {
    margin-top: 8px;
    font-weight: 300;
    font-size: 16px;
    color: var(--ink-soft);
  }
  .front-rule {
    position: absolute; left: 0; top: 158px;
    width: 262px; height: 4px;
    background: var(--accent);
  }
  .front-photo {
    position: absolute; left: 0; top: 162px;
    width: 262px; height: 172px;
    background: linear-gradient(160deg, var(--chair-white) 0%, var(--grass-light) 45%, var(--grass-dark) 100%);
  }
  .contact-panel {
    position: absolute; left: 262px; top: 0;
    width: 322px; height: 334px;
    background: linear-gradient(90deg, var(--card-shade), var(--card-white) 30%);
    border-left: 1px solid var(--rule);
    padding: 138px 24px 0 22px;
  }
  .company-line {
    font-size: 17px;
    color: var(--accent-deep);
    border-left: 2px solid var(--accent);
    padding-left: 10px;
    padding-bottom: 10px;
    border-bottom: 1px solid var(--rule);
  }
  .contact-list { list-style: none; }
  .contact-item {
    display: flex; align-items: center; gap: 12px;
    font-size: 15px;
    height: 44px;
    border-bottom: 1px solid var(--rule);
  }
  .contact-icon { width: 22px; height: 22px; flex: none; }

  /* ---------- back ---------- */
  .back-head {
    position: absolute; left: 0; top: 0;
    width: 100%; height: 196px;
    background: linear-gradient(180deg, var(--card-white), var(--card-shade));
    display: flex; flex-direction: column;
    align-items: center; justify-content: center;
  }
  .back-head .brand-name { font-size: 56px; }
  .back-head .brand-tagline { font-size: 24px; margin-top: 10px; }
  .back-rule {
    position: absolute; left: 0; top: 196px;
    width: 100%; height: 4px;
    background: var(--accent);
  }
  .back-photo {
    position: absolute; left: 0; top: 200px;
    width: 100%; height: 134px;
    background: linear-gradient(180deg, var(--grass-light), var(--grass-dark));
  }
</style>
</head>
<body>

<section class="card card-front">
  <div class="front-head">
    <p class="brand-name">Fern Lattice</p>
    <p class="brand-tagline">Table and Chair Rentals</p>
  </div>
  <div class="front-rule"></div>
  <div class="front-photo" role="img" aria-label="Photo of white folding chairs standing on green lawn"></div>

  <div class="contact-panel">
    <p class="company-line">Fernlattice Event Rentals, LLC</p>
    <ul class="contact-list">
      <li class="contact-item">
        <svg class="contact-icon" viewBox="0 0 22 22" aria-hidden="true">
          <circle cx="11" cy="11" r="10" fill="none" stroke="var(--accent)" stroke-width="1.5"/>
          <path d="M7.5 6.5l2 0 1 2.5-1.3 1a6 6 0 0 0 2.8 2.8l1-1.3 2.5 1v2a1 1 0 0 1-1 1A8 8 0 0 1 6.5 7.5a1 1 0 0 1 1-1z" fill="var(--accent)"/>
        </svg>
        <span>360-555-0182</span>
      </li>
      <li class="contact-item">
        <svg class="contact-icon" viewBox="0 0 22 22" aria-hidden="true">
          <circle cx="11" cy="11" r="10" fill="none" stroke="var(--accent)" stroke-width="1.5"/>
          <rect x="6" y="7" width="10" height="8" rx="1" fill="none" stroke="var(--accent)" stroke-width="1.4"/>
          <line x1="6" y1="9.5" x2="16" y2="9.5" stroke="var(--accent)" stroke-width="1.2"/>
        </svg>
        <span>www.fernlatticerentals.com</span>
      </li>
      <li class="contact-item">
        <svg class="contact-icon" viewBox="0 0 22 22" aria-hidden="true">
          <circle cx="11" cy="11" r="10" fill="none" stroke="var(--accent)" stroke-width="1.5"/>
          <rect x="6" y="7.5" width="10" height="7" fill="var(--accent)"/>
          <path d="M6 7.5l5 4 5-4" fill="none" stroke="#fff" stroke-width="1.2"/>
        </svg>
        <span>sales@fernlatticerentals.com</span>
      </li>
    </ul>
  </div>
</section>

<section class="card card-back">
  <div class="back-head">
    <p class="brand-name">Fern Lattice</p>
    <p class="brand-tagline">Table and Chair Rentals</p>
  </div>
  <div class="back-rule"></div>
  <div class="back-photo" role="img" aria-label="Photo of rows of white chairs on a lawn along a petal-strewn aisle"></div>
</section>

</body>
</html>
```